Tinker's Lamp sports bar beer & food menu

We need a menu design for our gastropub sports bar in L.A.'s Sawtelle Neighborhood (Little Osaka). We have a full-bar (hard liquor, craft beer, wine and cocktails) . We have a lunch and dinner menu as well as a happy hour menu. On Sundays we have a seperate menu with brunch items. The design concept is a British pub type of sports bar. We're looking for something different from our existing menu design. Ideally something cleaner and more legible. It should mesh a simple, modern sensibility with the more traditional darkened pub style of our interior design.

You can check out our Voxly page for photos of the interior/exterior:
https://www.reviewhatch.example/biz_photos/tinkers-lamp-los-angeles?tab=interior

You can view our existing menu here:
https://www.reviewhatch.example/biz_photos/tinkers-lamp-los-angeles?tab=menu

If there's an area of the design that can be a little more playful it's our highlighted event schedule so that the events will stand out.

Target Market(s)

Age of 25 and up. Sawtelle is a cultural hub that caters to a younger, moderately affluent crowd.

Industry/Entity Type

Sports Bar

Font styles to use
Sans Serif

Colors

Designer to choose colors to be used in the design.

Requirements
Must have
• Logo, highlighted event schedule (beer pong Monday, trivia Tuesday, taco Tuesday, whiskey Wednesday, karaoke Saturday). The menu should be easy to read in a darkened bar. We'll be printing on standard 8.5x11 in portrait.
Nice to have
• We're trying to have the menu take up as few pages as possible.
Should not have
• We're trying to have the menu take up as few pages as possible. Food photography isn't necessary. A cover isn't necessary. Please avoid clip art of food.

```html
<!DOCTYPE html>
<html lang="en">
<head>
<meta charset="utf-8">
<title>Tinker's Lamp — Burgers and Sandwiches</title>
<link rel="stylesheet" href="https://fonts.googleapis.com/css2?family=Nunito+Sans:wght@300;400;600&family=Playfair+Display+SC:wght@700&display=swap">
<style>
  :root {
    --bg: #0e1715;
    --text: #f4f4f2;
    --accent: #f2d27a;
    --banner: #d3d3d1;
    --banner-text: #141414;
    --photo-warm: #8a5a2c;
    --photo-dark: #1d1a17;
  }
  * { box-sizing: border-box; margin: 0; padding: 0; }
  html, body { width: 848px; height: 1200px; overflow: hidden; background: var(--bg); }
  .menu {
    position: relative;
    width: 848px; height: 1200px;
    background: var(--bg);
    color: var(--text);
    font-family: "Nunito Sans", Arial, sans-serif;
    font-weight: 300;
  }
  .brand {
    position: absolute; top: 26px; left: 0; right: 0;
    display: flex; flex-direction: column; align-items: center;
  }
  .brand-row { display: flex; align-items: center; gap: 16px; }
  .brand-mark { width: 46px; height: 46px; border: 4px solid var(--text); }
  .brand-name { font-size: 52px; font-weight: 400; line-height: 1; color: var(--text); }
  .brand-tag {
    margin-top: 10px; margin-left: 110px;
    font-size: 13px; letter-spacing: 4px; font-weight: 400;
  }
  .events {
    position: absolute; left: 92px; top: 130px; width: 686px; height: 69px;
    background: var(--banner); color: var(--banner-text);
    font-family: "Playfair Display SC", Georgia, serif; font-weight: 700;
    font-size: 18.5px; line-height: 27px; letter-spacing: 0.8px;
    display: flex; align-items: center; justify-content: center; text-align: center;
  }
  .photo { position: absolute; }
  .photo-burger {
    left: 30px; top: 226px; width: 376px; height: 315px;
    background: radial-gradient(circle at 55% 45%, #a8652f 0%, #6b4426 35%, var(--photo-dark) 80%);
  }
  .photo-fish {
    left: 424px; top: 838px; width: 402px; height: 338px;
    background: radial-gradient(circle at 45% 50%, #a9622a 0%, var(--photo-warm) 35%, var(--photo-dark) 85%);
  }
  .section-title {
    position: absolute; left: 424px; top: 214px;
    font-family: "Playfair Display SC", Georgia, serif; font-weight: 700;
    font-size: 23px; letter-spacing: 1.4px; color: var(--text);
  }
  .items { position: absolute; list-style: none; font-size: 20px; line-height: 34.2px; }
  .items-left { left: 30px; top: 563px; width: 376px; }
  .items-right { left: 423px; top: 259px; width: 404px; }
  .item-head { display: flex; align-items: baseline; color: var(--accent); }
  .item-leader { flex: 1; border-bottom: 1.5px dotted var(--accent); margin: 0 2px; transform: translateY(-5px); }
  .item-price { color: var(--text); }
  .item-desc { color: var(--text); }
</style>
</head>
<body>
<main class="menu">
  <header class="brand">
    <div class="brand-row">
      <span class="brand-mark"></span>
      <span class="brand-name">Tinker's Lamp</span>
    </div>
    <span class="brand-tag">PUB &amp; RESTAURANT</span>
  </header>

  <div class="events">Beer Pong Monday, Trivia &amp; Taco Tuesday, taco Tuesday,<br>Whiskey Wednesday, Karaoke Saturday</div>

  <div class="photo photo-burger" role="img" aria-label="Photo of a burger with crispy onions, served with fries, ketchup and a pickle"></div>

  <ul class="items items-left">
    <li><div class="item-head"><span>The Truffle Burger</span><span class="item-leader"></span><span class="item-price">$15</span></div>
      <p class="item-desc">Caramelized Onions, Arugula, Truffle Pecorino, Truffle Mayo and Truffle Fries</p></li>
    <li><div class="item-head"><span>The Sloppy Joe</span><span class="item-leader"></span><span class="item-price">$10</span></div>
      <p class="item-desc">Shredded Lettuce and Sharp Cheddar</p></li>
    <li><div class="item-head"><span>Veggie Burger</span><span class="item-leader"></span><span class="item-price">$12</span></div>
      <p class="item-desc">Concoction of kale, Tomato, Avocado, Sharp Cheddar with a Balsamic Reduction</p></li>
    <li><div class="item-head"><span>Flat Iron Steak Sandwich</span><span class="item-leader"></span><span class="item-price">$16</span></div>
      <p class="item-desc">Arugula, Peppers, Fontina, Onion and Mayo</p></li>
    <li><div class="item-head"><span>Chicken Spinach Wrap</span><span class="item-leader"></span><span class="item-price">$10</span></div>
      <p class="item-desc">Chicken, Bacon, Lettuce, Tomato, Avocado, Ranch and Mayo</p></li>
    <li><div class="item-head"><span>Fried Chicken Sliders (4)</span><span class="item-leader"></span><span class="item-price">$12</span></div>
      <p class="item-desc">Coleslaw, Lime Sriracha Sauce</p></li>
  </ul>

  <h2 class="section-title">BURGERS AND SANDWICHES</h2>

  <ul class="items items-right">
    <li><div class="item-head"><span>Chicken Sandwich</span><span class="item-leader"></span><span class="item-price">$12</span></div>
      <p class="item-desc">Chicken Breast, Applewood Bacon, Butter Lettuce, White Cheddar, Avocado and Tomato Served on Sourdough Bread</p></li>
    <li><div class="item-head"><span>Buttermilk Fried Chicken</span><span class="item-leader"></span><span class="item-price">$13</span></div>
      <p class="item-desc">Coleslaw, Provolone, Tomato, and a Spiced Mayonnaise on a Pretzel Roll</p></li>
    <li><div class="item-head"><span>Short Rib Sandwich</span><span class="item-leader"></span><span class="item-price">$13</span></div>
      <p class="item-desc">Beef Shorts, Mayo, Tomato, Caramelized Onions, Arugula, Pepper Jack Cheese Served on Sourdough Bread</p></li>
    <li><div class="item-head"><span>Grilled Cheese Sandwich</span><span class="item-leader"></span><span class="item-price">$10</span></div>
      <p class="item-desc">Cheese, Provolone and Cheddar Cheese</p></li>
    <li><div class="item-head"><span>Tinker's Lamp Burger</span><span class="item-leader"></span><span class="item-price">$14</span></div>
      <p class="item-desc">Sharp Cheddar, Arugula, Roasted Shallots, Bacon Jam with Malt Aioli</p></li>
  </ul>

  <div class="photo photo-fish" role="img" aria-label="Photo of battered fried fish with fries and a lemon wedge"></div>
</main>
</body>
</html>
```